Funky web design for eCommerce product site

This is the theme we want to use: http://marketstall.themevault-demo.test/home/home-product-landing-2/

The design must fit cleanly into the theme to minimise custom coding.

We are rebranding a health supplement product. 1 product, but comes in different quantities/packs.

The previous websites have been clunky, ugly, with poor design and very little purpose. We need a clean UI that takes the user through how it works, to the products, to the cart, all with a simple to use platform.

Tone of voice & Key Messages:

Funny, witty, relates to 28-40 audience. Product is for people who don't want to ruin their next day at work with a hangover OR cherish their weekends so much they would never want to waste a Saturday or Sunday. The characters telling the brand stories are two scientists

Full brief is attached with links to branding elements.

Target Market(s)

Men and women who love to drink alcohol and want to prevent hangovers.

Identified audience is 30-55 years (we will start by targeting 28-40), the USP is superior product performance based on health benefits of reduction of alcohol through the liver, secondarily hangover symptom reduction. Premium brand for health conscious consumers. Superior replacement for the go-to-hangover meds, ie. Feveril, Dolacin, Vitaroso - aids the process and digestion as opposed to inhibiting. Brand look and feel re-design to be relevant to identified target audience.

Industry/Entity Type

Health Product

Font styles to use
Other font styles liked:
• Norwester/Lato or Bangers/Oxygen

Colors

Designer to choose colors to be used in the design.

Requirements
Must have
• This site covers a lot of what we want: https://www.sitegrove-example.com.au/ecommerce-website-features/
• MOBILE FIRST DESIGN
• Video on homepage
• Email popup
• Add to cart from home page
• Coupon code
• Chatterbox Relay Chat
• Quick fill credit card info at checkout
• Reviews
• Mobile friendly
• Detailed shipping info (can be a secondary header bar with FREE shipping over $30 promo)
• Money back guarantee page (return policy)
• Contact page phone, email, and an online form + connect with us on Friendspace and Snapgrid
• Favicon
• Referral program
• SEO text boxes on home page
• Newsletter sign up in footer
• Sections to show: REVIEWS/TESTIMONIALS and REFER A FRIEND and MONEY BACK GUARANTEE
• Needs a call to action SHOP NOW button at the bottom of the page (see https://plumvo.example/)
• Needs payment icons in the footer (quidpass / Norda / Cardium for now)
• Colours and fonts should match branding guidelines.
Nice to have
• Loves design wise: https://postwren.example/
• Other inspiration
• https://www.boardlyn.example/pin/474285404494163209/
• https://www.boardlyn.example/pin/475200198166081933/
• https://www.boardlyn.example/pin/181692166197049862/
• https://www.boardlyn.example/pin/293156256984803604/
• https://www.boardlyn.example/pin/482025966346092082/
• https://www.boardlyn.example/pin/425238389801779277/
• http://fervent.kellotrap.example/
• https://brisklodge.example/
Should not have
• These are examples of the old site:
• http://www.hepranusa.example/
• http://demo.quarrywebworks.example/hepran-cms/
• We are moving away from the green
• These are examples of sites we do NOT want to see.

```html
<!DOCTYPE html>
<html lang="en">
<head>
<meta charset="utf-8">
<title>Hepran – Save Your Weekend</title>
<link rel="stylesheet" href="https://fonts.googleapis.com/css2?family=Bebas+Neue&family=Lato:wght@400;700;900&display=swap">
<style>
:root{
  --purple:#5a2d91;
  --purple-deep:#3b1c66;
  --teal:#3cc8d8;
  --ink:#1d1d24;
  --text:#4a4a55;
  --paper:#f4f4f6;
  --white:#ffffff;
  --footer:#16161c;
  --magenta:#c2338f;
  --cyan:#22b7d6;
  --veil:rgba(8,8,14,.68);
}
*{box-sizing:border-box;margin:0;padding:0}
html,body{width:1200px;height:4760px;overflow:hidden}
body{position:relative;background:var(--paper);font-family:"Lato",sans-serif;color:var(--text)}
h1,h2,h3,.logo,.btn{font-family:"Bebas Neue",sans-serif;letter-spacing:1px}
section,header,footer{position:absolute;left:0;width:1200px;overflow:hidden}
.btn{display:inline-block;background:var(--purple);color:var(--white);font-size:20px;padding:10px 30px;border-radius:22px}
p{font-size:17px;line-height:1.75}
.photo{position:absolute;border-radius:50%}

/* top bar + hero */
.promo-bar{top:0;height:40px;background:#101016;color:#cfcfd8;font-size:13px;text-align:center;line-height:40px;letter-spacing:1px}
.hero{top:40px;height:600px;background:linear-gradient(110deg,#2a2233 0%,#4b3a46 45%,#2b2430 100%)}
.site-nav{position:absolute;top:68px;left:100px;right:100px;display:flex;align-items:center}
.logo{font-size:46px;color:var(--white)}
.nav-links{display:flex;gap:40px;margin-left:70px;font-size:15px;color:#e8e8ee;font-weight:700}
.nav-icons{margin-left:auto;display:flex;gap:16px}
.nav-icons span{width:14px;height:14px;border-radius:50%;border:2px solid #e8e8ee}
.hero-copy{position:absolute;left:770px;top:220px;color:var(--white)}
.hero-copy h1{font-size:110px;line-height:1}
.hero-copy p{font-size:20px;line-height:1.5;margin:10px 0 28px;color:#e4dff0}

/* content sections */
.feature{height:540px;background:var(--paper)}
.feature h2{font-size:44px;color:var(--ink);margin-bottom:22px}
.feature .copy{position:absolute;top:150px;width:560px}
.feature .copy p{margin-bottom:18px}
.copy.left{left:120px}
.copy.right{left:520px}
.about{top:640px;height:500px}
.video{top:1140px;height:500px;background:linear-gradient(160deg,#8d8a88,#c9c2b8 55%,#6e6964)}
.play{position:absolute;left:560px;top:210px}
.how{top:1640px}
.science{top:2180px}
.refer{top:2720px;height:512px}
.coupon{font-weight:900;color:var(--ink)}
.reviews{top:3232px;height:440px;background:var(--purple-deep);text-align:center;color:var(--white)}
.reviews h2{font-size:44px;margin-top:70px}
.reviews blockquote{width:820px;margin:26px auto 0;font-size:18px;line-height:1.7;font-style:italic;color:#ddd3ef}
.reviewer{font-size:14px;margin-top:10px;color:#c6b9e0}
.product{top:3672px;height:600px}

/* footer */
.site-footer{top:4272px;height:488px;background:var(--footer);color:#b9b9c4}
.shop-now{position:absolute;left:180px;top:60px;width:240px;height:72px;background:var(--teal);color:var(--white);font-family:"Bebas Neue",sans-serif;font-size:34px;text-align:center;line-height:72px;letter-spacing:2px}
.newsletter{position:absolute;left:640px;top:34px;width:440px}
.newsletter h3{font-size:28px;color:var(--white);text-align:center;margin-bottom:12px}
.signup{display:flex}
.signup span{flex:1;height:44px;background:#2c2c35;color:#8a8a96;font-size:14px;line-height:44px;padding-left:16px}
.signup b{width:100px;background:var(--purple);color:var(--white);text-align:center;line-height:44px;font-size:14px}
.footer-links{position:absolute;top:236px;left:0;width:1200px;text-align:center;font-size:15px;letter-spacing:1px}
.payments{position:absolute;left:100px;top:278px;display:flex;gap:8px}
.payments span{background:#f2f2f5;color:var(--ink);font-size:13px;font-weight:700;padding:8px 10px;border-radius:3px}
.socials{position:absolute;left:0;width:1200px;top:296px;display:flex;justify-content:center;gap:30px;font-size:18px;font-weight:700;color:var(--white)}
.badges{position:absolute;right:90px;top:256px;display:flex;gap:30px}
.badges span{width:68px;height:68px;border-radius:50%;background:#d08a2a}
.badges span+span{background:#2e8bc7}
.copyright{position:absolute;left:0;width:1200px;top:440px;text-align:center;font-size:13px}

/* popup state */
.veil{position:absolute;inset:0;background:var(--veil)}
.email-popup{position:absolute;left:328px;top:204px;width:476px;height:436px;background:var(--white);border:18px solid var(--teal);border-radius:110px;text-align:center;padding-top:44px}
.email-popup .logo{color:var(--purple);font-size:54px}
.email-popup h3{font-family:"Lato",sans-serif;font-weight:900;font-size:17px;color:var(--ink);margin-top:6px}
.email-popup p{font-size:13px;line-height:1.6;width:300px;margin:10px auto 0;color:var(--text)}
.email-field{width:340px;height:46px;margin:22px auto 0;border:1px solid #cfcfd8;border-radius:23px;text-align:left;padding-left:20px;line-height:46px;font-size:13px;color:#8a8a96;box-shadow:0 2px 6px rgba(0,0,0,.12)}
.email-popup .btn{margin-top:20px;font-size:16px;padding:9px 30px}
</style>
</head>
<body>

<div class="promo-bar">FREE shipping on all orders over $30</div>

<header class="hero" role="img" aria-label="Night out scene with friends toasting drinks">
  <nav class="site-nav">
    <span class="logo">HEPRAN</span>
    <div class="nav-links"><span>Home</span><span>Shop</span><span>How It Works</span><span>Reviews</span><span>Refer</span><span>Contact</span></div>
    <div class="nav-icons"><span></span><span></span><span></span></div>
  </nav>
  <div class="hero-copy">
    <h1>HEPRAN</h1>
    <p>Save your Saturday. Keep your Monday.<br>Liver support for nights out.</p>
    <span class="btn">Shop Now</span>
  </div>
</header>

<svg width="0" height="0" style="position:absolute">
  <defs>
    <linearGradient id="prism" x1="0" y1="0" x2="1" y2="1">
      <stop offset="0" stop-color="#22b7d6"/><stop offset=".5" stop-color="#6b3fa6"/><stop offset="1" stop-color="#c2338f"/>
    </linearGradient>
  </defs>
</svg>

<section class="feature about">
  <svg style="position:absolute;right:0;top:0" width="260" height="500"><polygon points="260,0 260,500 60,250" fill="url(#prism)"/></svg>
  <div class="copy left">
    <h2>What is Hepran?</h2>
    <p>Hepran is a natural supplement that helps your liver process alcohol faster, so you can enjoy the night and still show up for the morning. Made by two scientists who got tired of losing weekends, it works with your body instead of masking the symptoms. Take it before, during or after a drink and wake up ready.</p>
    <span class="btn">Read More</span>
  </div>
  <div class="photo" role="img" aria-label="Portrait of a woman relaxing after a night out" style="left:740px;top:80px;width:320px;height:320px;background:radial-gradient(circle at 40% 40%,#b98a78,#3b2a30)"></div>
</section>

<section class="video" role="img" aria-label="Video still of a man asleep at his desk the morning after">
  <svg class="play" width="80" height="80" viewBox="0 0 80 80"><circle cx="40" cy="40" r="38" fill="rgba(20,20,28,.7)"/><polygon points="32,24 58,40 32,56" fill="#fff"/></svg>
</section>

<section class="feature how">
  <svg style="position:absolute;left:0;top:0" width="300" height="540"><polygon points="0,0 0,540 240,270" fill="url(#prism)"/></svg>
  <div class="photo" role="img" aria-label="Portrait of a scientist in a suit" style="left:128px;top:110px;width:320px;height:320px;background:radial-gradient(circle at 50% 40%,#c9c9cc,#3a3a40)"></div>
  <div class="copy right" style="top:160px">
    <h2>How does Hepran work ?</h2>
    <p>Our blend of vitamins and plant extracts supports the enzymes that break alcohol down, helping your body clear it before it turns into a headache.</p>
    <p>No more trading tomorrow for tonight. Just one sachet and a glass of water.</p>
    <span class="btn">Read More</span>
  </div>
</section>

<section class="feature science">
  <svg style="position:absolute;right:0;top:0" width="260" height="540"><polygon points="260,0 260,540 70,270" fill="url(#prism)"/></svg>
  <div class="copy left" style="top:150px">
    <h2>Hangover Science</h2>
    <p>When you drink, your liver turns alcohol into acetaldehyde, the real villain behind the pounding head and the queasy stomach. Hepran gives your liver the tools to move it along quickly, so less of it sticks around to ruin your day.</p>
    <span class="btn">Read More</span>
  </div>
  <div class="photo" role="img" aria-label="Man lying in bed with a hangover" style="left:760px;top:100px;width:320px;height:320px;background:radial-gradient(circle at 45% 45%,#8a8088,#2d2830)"></div>
</section>

<section class="feature refer">
  <svg style="position:absolute;left:0;top:0" width="300" height="512"><polygon points="0,0 0,512 230,256" fill="url(#prism)"/></svg>
  <div class="photo" role="img" aria-label="Group of friends celebrating together" style="left:128px;top:100px;width:320px;height:320px;background:radial-gradient(circle at 50% 45%,#d4d4d8,#4a4a52)"></div>
  <div class="copy right" style="top:110px">
    <h2>Refer a Friend</h2>
    <p>Good friends share their secrets. Send a friend your code and you both get 15% off your next order of Hepran.</p>
    <p class="coupon">Coupon code : HEPRAN15</p>
    <span class="btn">Refer Now</span>
  </div>
</section>

<section class="reviews">
  <h2>Reviews</h2>
  <blockquote>“I used to write off every Sunday after a big Saturday. Now I'm up for brunch and a run. Hepran is part of my night out kit.”</blockquote>
  <div role="img" aria-label="Reviewer portrait" style="width:100px;height:100px;border-radius:50%;margin:26px auto 0;border:3px solid #fff;background:radial-gradient(circle,#b79c8a,#4a3a40)"></div>
  <div class="reviewer">Daniel Carter</div>
</section>

<section class="feature product">
  <svg style="position:absolute;right:0;top:0" width="300" height="600"><polygon points="300,0 300,600 60,300" fill="url(#prism)"/></svg>
  <div class="copy left" style="top:140px">
    <h2>Our Product</h2>
    <p>One product, three pack sizes. Pick the 6, 12 or 30 sachet pack and keep one in your bag, your desk and your car. Free shipping on orders over $30.</p>
    <span class="btn">Add to Cart</span>
  </div>
  <div role="img" aria-label="Hepran supplement box and sachets" style="position:absolute;left:800px;top:170px;width:270px;height:260px;background:linear-gradient(135deg,#6fce6a,#2f8f3b);box-shadow:8px 8px 0 rgba(0,0,0,.12)"></div>
</section>

<footer class="site-footer">
  <div class="shop-now">Shop Now</div>
  <div class="newsletter">
    <h3>Newsletter</h3>
    <div class="signup"><span>Your email address</span><b>Join</b></div>
  </div>
  <div class="footer-links">Privacy &nbsp;|&nbsp; Shipping &nbsp;|&nbsp; Returns &nbsp;|&nbsp; Contact</div>
  <div class="payments"><span>Norda</span><span>Cardium</span><span>quidpass</span></div>
  <div class="socials"><span>Friendspace</span><span>Snapgrid</span></div>
  <div class="badges"><span></span><span></span></div>
  <div class="copyright">Copyright 2024 Hepran. All rights reserved.</div>
</footer>

<div class="veil"></div>

<div class="email-popup">
  <div class="logo">HEPRAN</div>
  <h3>SEE HOW YOU CAN TRY HEPRAN FOR FREE TODAY!</h3>
  <p>Register your email for discount offers and get access to awesome prizes and FREE samples!</p>
  <div class="email-field">Email id</div>
  <span class="btn">Subscribe</span>
</div>

</body>
</html>
```